Lumora Systems New Website - IT Infrastructure | Smart Cabinet | Micro Data Center

We're an IT SI providing Server Room Design & Build | All-in-One Rack & Smart Cabinet | Structured Cabling | IT Relocation | Maintenance. Old website can be found at www.lumorasys.com.hk. We'd like a brand new wix website which is modern, minimalist, interactive with some animation. Website content will be mostly static and include our service, our project, news and events, about us, contacts, blogs, partners and brands, etc.

reference sites:
We'd like to see more designs referring to below

https://www.pixelvane.example/design/41736205
https://www.pixelvane.example/design/41892417
https://velbrinn.example/

Animation (scrolling effect) referring to
https://velbrinn.example/intelligence/smart-office-room/
Updates

we'd like below style.

Designs look the same

Target Market(s)

Commercials in HK

Industry/Entity Type

IT, Technology, Data Center

Coding

Coded - Design and coding required

Font styles to use
Sans Serif

Requirements
Must have
• CMS, Some Interactive Elements/ Graphics

```html
<!DOCTYPE html>
<html lang="en">
<head>
<meta charset="utf-8">
<title>Lumora Systems – IT Infrastructure</title>
<link rel="stylesheet" href="https://fonts.googleapis.com/css2?family=Open+Sans:wght@400;600;700&family=Tinos:wght@400;700&display=swap">
<style>
:root{
  --navy:#2d3567;
  --orange:#f77a0c;
  --lavender:#efeef8;
  --lavender-2:#e4e2f3;
  --ink:#2e3452;
  --grey:#858894;
  --line:#dcdbe6;
  --dark:#272b38;
  --white:#ffffff;
  --sans:'Open Sans', Arial, sans-serif;
  --serif:'Tinos', 'Times New Roman', serif;
}
*{box-sizing:border-box;margin:0;padding:0}
html,body{width:1200px;height:5252px;overflow:hidden;background:var(--white);font-family:var(--sans);color:var(--ink)}
.abs{position:absolute}
section,header,footer{position:relative;width:1200px;overflow:hidden}
.serif-title{font-family:var(--serif);font-weight:400;color:var(--navy);text-align:center;font-size:46px;line-height:1}
.lede{font-size:13px;line-height:23px;color:var(--grey);text-align:center}

/* header */
.site-header{height:124px;background:var(--white)}
.contact-chip{display:flex;align-items:center;gap:12px;top:18px}
.chip-icon{width:30px;height:30px;border-radius:50%;background:var(--navy);display:flex;align-items:center;justify-content:center}
.chip-text{font-size:10px;line-height:13px;color:var(--grey)}
.chip-text b{display:block;color:var(--ink);font-weight:600}
.brand{left:500px;top:36px;width:200px;text-align:center}
.brand-name{font-size:24px;font-weight:600;color:var(--orange)}
.appt-btn{left:880px;top:12px;width:184px;height:38px;border-radius:19px;background:var(--navy);color:var(--white);font-size:11px;font-weight:700;display:flex;align-items:center;justify-content:center;letter-spacing:.3px}
.main-nav a{position:absolute;top:84px;font-size:11px;color:var(--ink);text-decoration:none}

/* hero */
.hero{height:840px}
.hero-photo{position:absolute;inset:0;background:
  radial-gradient(ellipse at 80% 40%, rgba(245,130,40,.35), transparent 45%),
  radial-gradient(ellipse at 15% 20%, rgba(90,120,190,.5), transparent 55%),
  linear-gradient(120deg,#1e2547 0%,#2f3a6a 45%,#43507e 70%,#1a1f3b 100%)}
.hero-eyebrow{left:88px;top:208px;font-size:15px;letter-spacing:3.5px;color:var(--white);font-weight:600}
.hero-title{left:86px;top:235px;font-size:45px;line-height:60px;font-weight:700;color:var(--white)}
.hero-rule{left:88px;top:369px;width:632px;height:1px;background:rgba(255,255,255,.6)}
.hero-copy{left:88px;top:398px;width:620px;font-size:15px;line-height:27px;color:var(--white);font-weight:600}
.btn{position:absolute;height:40px;border-radius:20px;font-size:14px;font-weight:700;display:flex;align-items:center;justify-content:center}
.btn-navy{left:82px;top:487px;width:146px;background:var(--navy);color:var(--white)}
.btn-light{left:240px;top:487px;width:180px;background:var(--white);color:var(--navy)}
.scroll-badge{width:56px;height:56px;border-radius:50%;background:var(--white);box-shadow:0 4px 14px rgba(0,0,0,.15);display:flex;align-items:center;justify-content:center}

/* about */
.about{height:584px}
.about-ring{left:86px;top:30px;width:460px;height:460px;border-radius:50%;border:4px solid var(--navy);border-left-color:transparent;border-bottom-color:transparent;transform:rotate(-10deg)}
.about-photo{left:96px;top:40px;width:440px;height:440px;border-radius:50%;background:linear-gradient(135deg,#3b4a74,#8893b3 55%,#d9dce7)}
.eyebrow-sm{left:620px;top:60px;font-family:var(--serif);font-size:16px;color:var(--ink)}
.about-title{left:620px;top:84px;font-family:var(--serif);font-weight:400;font-size:46px;line-height:54px;color:var(--navy)}
.about-quote{left:620px;top:205px;width:460px;border-left:3px solid var(--lavender-2);padding:4px 0 4px 16px;font-size:12px;line-height:23px;color:var(--grey)}
.about-copy{left:620px;top:285px;width:470px;font-size:12px;line-height:23px;color:var(--grey)}
.btn-orange{position:absolute;left:620px;top:435px;width:155px;height:44px;background:var(--orange);color:var(--white);font-size:15px;font-weight:700;display:flex;align-items:center;justify-content:center;gap:10px}

/* services */
.services{height:570px;background:var(--lavender)}
.service-card{position:absolute;top:236px;width:319px;height:269px;border-radius:6px;overflow:hidden}
.service-card .photo{position:absolute;inset:0}
.service-card h3{position:absolute;left:20px;top:64px;font-family:var(--serif);font-size:28px;font-weight:700;color:var(--white)}
.service-icon{position:absolute;top:200px;width:72px;height:72px;border-radius:50%;background:var(--white);display:flex;align-items:center;justify-content:center;box-shadow:0 3px 10px rgba(0,0,0,.08)}

/* why */
.why{height:730px}
.why-bubble{width:430px;height:430px;border-radius:50%;background:linear-gradient(90deg,var(--white),var(--lavender) 60%)}
.why-portrait{left:411px;top:239px;width:380px;height:380px;border-radius:50%;background:linear-gradient(160deg,#525d84,#8d97b8 50%,#3a4467)}
.why-icon{position:absolute;width:86px;height:86px;border-radius:50%;background:var(--white);box-shadow:0 0 0 3px #f4d2b4;display:flex;align-items:center;justify-content:center}
.why-icon i{width:66px;height:66px;border-radius:50%;background:var(--navy);display:flex;align-items:center;justify-content:center}
.why-item{position:absolute;width:240px}
.why-item h4{font-family:var(--serif);font-weight:400;font-size:21px;color:var(--navy);margin-bottom:8px}
.why-item p{font-size:12px;line-height:23px;color:var(--grey)}
.why-left{text-align:right}

/* projects */
.projects{height:702px;background:var(--lavender)}
.slide{position:absolute;top:245px;height:402px}
.slide-main{left:234px;width:732px;background:linear-gradient(160deg,#5a6179,#8c92a5 45%,#2b3042)}
.slide-caption{position:absolute;left:36px;bottom:22px;width:620px;font-size:16px;line-height:24px;color:var(--white)}
.slide-arrow{position:absolute;top:433px;width:40px;height:40px;border-radius:50%;background:#f0453a;display:flex;align-items:center;justify-content:center}

/* contact */
.contact{height:559px}
.contact-bg{position:absolute;inset:0;background:linear-gradient(100deg,#1d2238,#2c3553 50%,#4f5a7a)}
.hours-title{left:94px;top:135px;font-family:var(--serif);font-weight:400;font-size:27px;color:var(--white)}
.hours-bar{left:96px;top:196px;width:4px;height:228px;background:var(--orange)}
.hours-row{position:absolute;left:133px;width:418px;height:51px;display:flex;justify-content:space-between;align-items:center;font-size:14px;color:var(--white);border-bottom:1px solid rgba(255,255,255,.15)}
.hours-row b{font-weight:700}
.form-panel{left:612px;top:26px;width:491px;height:500px;background:#f3f2f8}
.form-head{position:absolute;left:55px;top:44px;display:flex;align-items:center;gap:22px}
.form-head i{width:52px;height:52px;border-radius:50%;background:var(--navy);display:flex;align-items:center;justify-content:center}
.form-head h3{font-family:var(--serif);font-weight:400;font-size:33px;color:var(--navy)}
.field{position:absolute;height:51px;background:var(--white);border:1px solid var(--line);font-size:13px;color:var(--grey);padding-left:26px;display:flex;align-items:center}
.submit{position:absolute;left:55px;top:422px;width:385px;height:53px;background:var(--orange);color:var(--white);font-size:19px;font-weight:700;display:flex;align-items:center;justify-content:center;letter-spacing:.5px}

/* reviews */
.reviews{height:619px}
.review-card{position:absolute;top:273px;width:320px;height:271px;background:var(--white);box-shadow:0 4px 22px rgba(45,53,103,.1)}
.review-card.active{border-bottom:5px solid var(--navy)}
.avatar{position:absolute;left:29px;top:-32px;width:62px;height:62px;border-radius:50%;background:linear-gradient(160deg,#c9cbd6,#8f95ad);border:4px solid var(--white)}
.quote-mark{position:absolute;right:26px;top:-12px;font-family:var(--serif);font-size:96px;line-height:1;color:#f6c49a;font-weight:700}
.stars{position:absolute;left:26px;top:64px;color:var(--orange);font-size:16px;letter-spacing:3px}
.review-text{position:absolute;left:26px;top:92px;width:270px;font-size:12px;line-height:23px;color:var(--grey)}
.review-name{position:absolute;left:26px;top:192px;font-family:var(--serif);font-size:19px;color:var(--navy)}
.review-role{position:absolute;left:26px;top:219px;font-size:9px;color:var(--grey);letter-spacing:.5px}

/* footer */
.site-footer{height:522px;background:var(--dark)}
.footer-brand{left:0;top:176px;width:1200px;text-align:center}
.footer-brand .brand-name{font-size:36px}
.footer-nav a{position:absolute;top:280px;font-size:14px;font-weight:600;color:var(--white);text-decoration:none}
.footer-rule{left:143px;top:334px;width:915px;height:1px;background:rgba(255,255,255,.3)}
.footer-info{position:absolute;top:370px;display:flex;align-items:center;gap:18px;color:var(--white);font-size:11px;line-height:16px}
.footer-info i{width:58px;height:58px;border-radius:50%;border:2px solid rgba(255,255,255,.75);display:flex;align-items:center;justify-content:center;flex:none}
.footer-info b{display:block;font-size:14px;font-weight:600}
.footer-sep{position:absolute;top:368px;width:1px;height:62px;background:rgba(255,255,255,.4)}
.bottom-bar{left:0;top:465px;width:1200px;height:57px;background:var(--navy)}
.bottom-bar p{position:absolute;left:153px;top:20px;font-size:12px;color:var(--white);font-weight:600}
.social{position:absolute;top:17px;width:24px;height:24px;border:1.5px solid var(--white);border-radius:3px}
</style>
</head>
<body>

<header class="site-header">
  <div class="abs contact-chip" style="left:122px">
    <span class="chip-icon"><svg width="14" height="14" viewBox="0 0 24 24"><path d="M6.6 10.8a15 15 0 0 0 6.6 6.6l2.2-2.2a1 1 0 0 1 1-.25 11.4 11.4 0 0 0 3.6.57 1 1 0 0 1 1 1V20a1 1 0 0 1-1 1A17 17 0 0 1 3 4a1 1 0 0 1 1-1h3.5a1 1 0 0 1 1 1c0 1.25.2 2.45.57 3.57a1 1 0 0 1-.25 1z" fill="#fff"/></svg></span>
    <span class="chip-text"><b>Call Us:</b>+852 2345 6789</span>
  </div>
  <div class="abs contact-chip" style="left:280px">
    <span class="chip-icon"><svg width="14" height="14" viewBox="0 0 24 24"><rect x="3" y="6" width="18" height="12" rx="1.5" fill="none" stroke="#fff" stroke-width="2"/><path d="M3 7l9 6 9-6" fill="none" stroke="#fff" stroke-width="2"/></svg></span>
    <span class="chip-text"><b>Email:</b>hello@lumorasys.com.hk</span>
  </div>
  <div class="abs brand"><span class="brand-name">Lumora Systems</span></div>
  <div class="abs appt-btn">MAKE APPOINTMENT</div>
  <nav class="main-nav">
    <a style="left:132px">Home</a><a style="left:243px">About Us</a><a style="left:394px">Services</a>
    <a style="left:712px">Our Team</a><a style="left:840px">Gallery</a><a style="left:964px">Contact Us</a>
  </nav>
</header>

<section class="hero">
  <div class="hero-photo" role="img" aria-label="Data centre server aisle with glowing racks and cabling"></div>
  <div class="abs hero-eyebrow">DATA INFRASTRUCTURE</div>
  <h1 class="abs hero-title">Pioneering Tomorrow's<br>Digital Landscape</h1>
  <div class="abs hero-rule"></div>
  <p class="abs hero-copy">Lorem ipsum dolor sit amet, consectetur adipiscing elit et dolore conser tempor incididunt ut labore et dolore magna</p>
  <div class="btn btn-navy">LEARN MORE</div>
  <div class="btn btn-light">REQUEST QUOTE</div>
  <svg class="abs" style="left:0;top:0" width="1200" height="840" viewBox="0 0 1200 840">
    <path d="M0 660 Q600 824 1200 660 L1200 840 L0 840Z" fill="#fff"/>
  </svg>
  <div class="abs scroll-badge" style="left:572px;top:738px">
    <svg width="18" height="12" viewBox="0 0 18 12"><path d="M2 3l7 7 7-7" fill="none" stroke="var(--orange)" stroke-width="2.5" stroke-linecap="round"/></svg>
  </div>
</section>

<section class="about">
  <div class="abs about-ring"></div>
  <div class="abs about-photo" role="img" aria-label="Smiling engineer in a server room"></div>
  <div class="abs eyebrow-sm">Data Infrastructure</div>
  <h2 class="abs about-title">Catalyst for Digital<br>Evolution</h2>
  <p class="abs about-quote">Lorem ipsum dolor sit amet, consectetur adipiscing elit, sed do eiusmod tempor incididunt ut labore et dolore</p>
  <p class="abs about-copy">Lorem ipsum dolor sit amet, consectetur adipiscing elit, sed do eiusmod tempor incididunt ut labore et dolore magna aliqua. Ut enim ad minim veniam, quis nostrud exercitation ullamco laboris nisi ut aliquip ex ea commodo consequat. Duis aute irure dolor in reprehenderit in voluptate velit esse cillum dolore eu fugiat nulla pariatur. Excepteur</p>
  <div class="btn-orange">Learn More
    <svg width="18" height="12" viewBox="0 0 18 12"><path d="M1 6h15M11 1l5 5-5 5" fill="none" stroke="#fff" stroke-width="2"/></svg>
  </div>
</section>

<section class="services">
  <h2 class="serif-title abs" style="left:0;width:1200px;top:70px">Our Services</h2>
  <p class="lede abs" style="left:350px;width:500px;top:125px">Lorem ipsum dolor sit amet, consectetur adipiscing elit, sed do eiusmod temp or incididunt ut labore et dolore</p>

  <div class="service-card" style="left:92px">
    <div class="photo" role="img" aria-label="Technician with laptop in data centre" style="background:linear-gradient(160deg,#2a3466,#4c5d96 50%,#1c2246)"></div>
    <h3>Data Centre Building</h3>
  </div>
  <div class="service-card" style="left:438px">
    <div class="photo" role="img" aria-label="Engineer working on cabling at a rack" style="background:linear-gradient(160deg,#1f2540,#4a5477 50%,#242a45)"></div>
    <h3>Structured Cabling</h3>
  </div>
  <div class="service-card" style="left:787px">
    <div class="photo" role="img" aria-label="Blue-lit server racks" style="background:linear-gradient(160deg,#263a78,#4d6cc0 50%,#1c2a5c)"></div>
    <h3>Audio-Visual</h3>
  </div>

  <div class="service-icon" style="left:133px"><svg width="30" height="30" viewBox="0 0 24 24"><path d="M4 20V12M9 20V8M14 20v-6M19 20V10" stroke="var(--orange)" stroke-width="2.5" stroke-linecap="round"/></svg></div>
  <div class="service-icon" style="left:482px"><svg width="30" height="30" viewBox="0 0 24 24"><circle cx="12" cy="12" r="9" fill="none" stroke="var(--orange)" stroke-width="1.5"/><circle cx="12" cy="12" r="5" fill="none" stroke="var(--orange)" stroke-width="1.5"/><circle cx="12" cy="12" r="2" fill="var(--orange)"/></svg></div>
  <div class="service-icon" style="left:829px"><svg width="30" height="30" viewBox="0 0 24 24"><path d="M10 12V5a2 2 0 0 1 4 0v7h2a3 3 0 0 1 3 3v3a3 3 0 0 1-3 3h-5l-4-5 1-1 2 1" fill="none" stroke="var(--orange)" stroke-width="1.8" stroke-linejoin="round"/></svg></div>
</section>

<section class="why">
  <h2 class="serif-title abs" style="left:0;width:1200px;top:82px">Why Choose Us</h2>
  <p class="lede abs" style="left:350px;width:500px;top:130px">Lorem ipsum dolor sit amet, consectetur adipiscing elit, sed do eiusmod temp or incididunt ut labore et dolore</p>

  <div class="abs why-bubble" style="left:240px;top:230px"></div>
  <div class="abs why-bubble" style="left:530px;top:230px;background:linear-gradient(270deg,#fff,var(--lavender) 60%)"></div>
  <div class="abs why-portrait" role="img" aria-label="Smiling businessman with crossed arms"></div>

  <div class="why-item why-left" style="left:135px;top:275px"><h4>Professional</h4><p>Lorem ipsum dolor sit amet, consectet ur adipiscing elit et dolore conser</p></div>
  <div class="why-item why-left" style="left:135px;top:407px"><h4>Scalable Infrastructure</h4><p>Lorem ipsum dolor sit amet, consectet ur adipiscing elit et dolore conser</p></div>
  <div class="why-item why-left" style="left:135px;top:540px"><h4>Personal Approach</h4><p>Lorem ipsum dolor sit amet, consectet ur adipiscing elit et dolore conser</p></div>
  <div class="why-item" style="left:797px;top:275px"><h4>Experienced Experts</h4><p>Lorem ipsum dolor sit amet, consectet ur adipiscing elit et dolore conser</p></div>
  <div class="why-item" style="left:797px;top:407px"><h4>Proven Track Record</h4><p>Lorem ipsum dolor sit amet, consectet ur adipiscing elit et dolore conser</p></div>
  <div class="why-item" style="left:797px;top:540px"><h4>Quality Services</h4><p>Lorem ipsum dolor sit amet, consectet ur adipiscing elit et dolore conser</p></div>

  <div class="why-icon" style="left:395px;top:276px"><i><svg width="28" height="28" viewBox="0 0 24 24"><circle cx="12" cy="5" r="2" fill="#fff"/><path d="M5 9h14M12 9v6M8 21l4-6 4 6" fill="none" stroke="#fff" stroke-width="2" stroke-linecap="round"/></svg></i></div>
  <div class="why-icon" style="left:395px;top:408px"><i><svg width="28" height="28" viewBox="0 0 24 24"><g stroke="#fff" stroke-width="2" stroke-linecap="round"><path d="M12 3v3M12 18v3M3 12h3M18 12h3M5.6 5.6l2.1 2.1M16.3 16.3l2.1 2.1M5.6 18.4l2.1-2.1M16.3 7.7l2.1-2.1"/></g></svg></i></div>
  <div class="why-icon" style="left:395px;top:541px"><i><svg width="28" height="28" viewBox="0 0 24 24"><path d="M4 12a8 8 0 0 1 14-5M20 12a8 8 0 0 1-14 5M4 13h16" fill="none" stroke="#fff" stroke-width="2" stroke-linecap="round"/></svg></i></div>
  <div class="why-icon" style="left:692px;top:276px"><i><svg width="28" height="28" viewBox="0 0 24 24"><circle cx="12" cy="12" r="8" fill="none" stroke="#fff" stroke-width="1.5"/><circle cx="12" cy="12" r="4" fill="none" stroke="#fff" stroke-width="1.5"/><circle cx="12" cy="12" r="1.5" fill="#fff"/></svg></i></div>
  <div class="why-icon" style="left:692px;top:408px"><i><svg width="28" height="28" viewBox="0 0 24 24"><path d="M4 12a8 8 0 0 1 14-5M20 12a8 8 0 0 1-14 5M4 13h16" fill="none" stroke="#fff" stroke-width="2" stroke-linecap="round"/></svg></i></div>
  <div class="why-icon" style="left:692px;top:541px"><i><svg width="28" height="28" viewBox="0 0 24 24"><g fill="none" stroke="#fff" stroke-width="2"><rect x="3" y="3" width="5" height="5"/><rect x="16" y="3" width="5" height="5"/><rect x="3" y="16" width="5" height="5"/><rect x="16" y="16" width="5" height="5"/><path d="M8 5.5h8M8 18.5h8M5.5 8v8"/></g></svg></i></div>
</section>

<section class="projects">
  <h2 class="serif-title abs" style="left:0;width:1200px;top:92px">Our Recent Projects</h2>
  <p class="lede abs" style="left:350px;width:500px;top:140px">Lorem ipsum dolor sit amet, consectetur adipiscing elit, sed do eiusmod temp or incididunt ut labore et dolore</p>

  <div class="slide" style="left:0;width:206px;background:linear-gradient(140deg,#2c4fa8,#6a92e0 45%,#24347a 80%,#b24a5a)" role="img" aria-label="Close-up of blue server units"></div>
  <div class="slide slide-main" role="img" aria-label="Technician kneeling beside open server racks">
    <p class="slide-caption">Lorem ipsum dolor sit amet, consecteturipsum dolor sit amet, consectetur amet, consectetur</p>
  </div>
  <div class="slide" style="left:995px;width:205px;background:linear-gradient(160deg,#101a30,#2a4f7a 50%,#0d1526)" role="img" aria-label="Dark data hall with blue lights"></div>

  <div class="slide-arrow" style="left:178px"><svg width="16" height="14" viewBox="0 0 16 14"><path d="M15 7H2M7 1L1 7l6 6" fill="none" stroke="#fff" stroke-width="2"/></svg></div>
  <div class="slide-arrow" style="left:983px"><svg width="16" height="14" viewBox="0 0 16 14"><path d="M1 7h13M9 1l6 6-6 6" fill="none" stroke="#fff" stroke-width="2"/></svg></div>
</section>

<section class="contact">
  <div class="contact-bg" role="img" aria-label="Dim server room background"></div>
  <h3 class="abs hours-title">Open Hours</h3>
  <div class="abs hours-bar"></div>
  <div class="hours-row" style="top:208px"><b>Monday - Friday</b><span>08am - 05pm</span></div>
  <div class="hours-row" style="top:259px"><b>Saturday</b><span>08am - 05pm</span></div>
  <div class="hours-row" style="top:310px"><b>Telephone</b><span>+123 456 7890</span></div>
  <div class="hours-row" style="top:361px;border-bottom:none"><b>Email</b><span>info@lumorasys.com.hk</span></div>

  <div class="abs form-panel">
    <div class="form-head"><i><svg width="24" height="24" viewBox="0 0 24 24"><rect x="3" y="6" width="18" height="12" rx="1.5" fill="none" stroke="#fff" stroke-width="1.6"/><path d="M3 7l9 6 9-6" fill="none" stroke="#fff" stroke-width="1.6"/></svg></i><h3>Get in touch with us</h3></div>
    <div class="field" style="left:55px;top:135px;width:181px">First Name</div>
    <div class="field" style="left:256px;top:135px;width:184px">Last Name</div>
    <div class="field" style="left:55px;top:206px;width:181px">Email Address</div>
    <div class="field" style="left:256px;top:206px;width:184px">Phone Number</div>
    <div class="field" style="left:55px;top:280px;width:385px">Select Subject</div>
    <div class="field" style="left:55px;top:353px;width:385px">dd/mm/yyyy</div>
    <div class="submit">SUBMIT</div>
  </div>
</section>

<section class="reviews">
  <h2 class="serif-title abs" style="left:0;width:1200px;top:88px">Clients Reviews</h2>
  <p class="lede abs" style="left:350px;width:500px;top:136px">Lorem ipsum dolor sit amet, consectetur adipiscing elit, sed do eiusmod temp or incididunt ut labore et dolore</p>

  <div class="review-card" style="left:102px">
    <div class="avatar" role="img" aria-label="Client portrait"></div><div class="quote-mark">”</div>
    <div class="stars">★★★★★</div>
    <p class="review-text">Lorem ipsum dolor sit amet, consectetur adipiscing elit, sed do eiusmod tempor inci didunt ut labore et dolore magna aliqua. Ut enim ad minim veniam, quis</p>
    <div class="review-name">Nadia Corvell</div><div class="review-role">BUSINESSMAN</div>
  </div>
  <div class="review-card active" style="left:446px">
    <div class="avatar" role="img" aria-label="Client portrait"></div><div class="quote-mark" style="color:var(--orange)">”</div>
    <div class="stars">★★★★★</div>
    <p class="review-text">Lorem ipsum dolor sit amet, consectetur adipiscing elit, sed do eiusmod tempor inci didunt ut labore et dolore magna aliqua. Ut enim ad minim veniam, quis</p>
    <div class="review-name">Nadia Corvell</div><div class="review-role">BUSINESSMAN</div>
  </div>
  <div class="review-card" style="left:791px">
    <div class="avatar" role="img" aria-label="Client portrait"></div><div class="quote-mark">”</div>
    <div class="stars">★★★★★</div>
    <p class="review-text">Lorem ipsum dolor sit amet, consectetur adipiscing elit, sed do eiusmod tempor inci didunt ut labore et dolore magna aliqua. Ut enim ad minim veniam, quis</p>
    <div class="review-name">Nadia Corvell</div><div class="review-role">BUSINESSMAN</div>
  </div>
</section>

<footer class="site-footer">
  <svg class="abs" style="left:0;top:0" width="1200" height="120" viewBox="0 0 1200 120">
    <path d="M0 0 H1200 Q600 150 0 0Z" fill="#fff"/>
  </svg>
  <div class="abs scroll-badge" style="left:572px;top:48px">
    <svg width="18" height="12" viewBox="0 0 18 12"><path d="M2 10l7-7 7 7" fill="none" stroke="var(--orange)" stroke-width="2.5" stroke-linecap="round"/></svg>
  </div>

  <div class="abs footer-brand brand-wrap"><span class="brand-name" style="font-size:36px;font-weight:600;color:var(--orange)">Lumora Systems</span></div>
  <nav class="footer-nav">
    <a style="left:358px">HOME</a><a style="left:450px">SERVICES</a><a style="left:556px">ABOUT US</a>
    <a style="left:676px">TESTIMONIALS</a><a style="left:826px">BLOG</a>
  </nav>
  <div class="abs footer-rule"></div>

  <div class="footer-info" style="left:172px">
    <i><svg width="28" height="28" viewBox="0 0 24 24"><circle cx="12" cy="12" r="9" fill="none" stroke="#fff" stroke-width="1.5"/><path d="M3 12h18M12 3c3 3 3 15 0 18M12 3c-3 3-3 15 0 18" fill="none" stroke="#fff" stroke-width="1.5"/></svg></i>
    <span>123, Building Name, Street<br>City, State XY 123456</span>
  </div>
  <div class="footer-sep" style="left:430px"></div>
  <div class="footer-info" style="left:505px">
    <i><svg width="22" height="28" viewBox="0 0 16 24"><rect x="2" y="1" width="12" height="22" rx="2" fill="none" stroke="#fff" stroke-width="1.5"/><circle cx="8" cy="19" r="1" fill="#fff"/></svg></i>
    <span><b>PHONE</b>(123) 456 7890</span>
  </div>
  <div class="footer-sep" style="left:750px"></div>
  <div class="footer-info" style="left:825px">
    <i><svg width="26" height="26" viewBox="0 0 24 24"><rect x="3" y="6" width="18" height="12" rx="1.5" fill="none" stroke="#fff" stroke-width="1.5"/><path d="M3 7l9 6 9-6" fill="none" stroke="#fff" stroke-width="1.5"/></svg></i>
    <span><b>EMAIL</b>info@lumorasys.com.hk</span>
  </div>

  <div class="abs bottom-bar">
    <p>Lumora Systems</p>
    <span class="social" style="left:935px"></span>
    <span class="social" style="left:966px"></span>
    <span class="social" style="left:997px"></span>
    <span class="social" style="left:1028px"></span>
  </div>
</footer>

</body>
</html>
```